Sales Deck Redesign for a B2B business selling customer service AI products

We are looking for a redesign of our sales Deck. we are a B2B business selling customer service AI products.

The sales deck is attached, we would like this to be made less "powerpoint" and more "professional expertise in a friendly package".

Our brand standards are attached with details on logos, colours and imagery.

Other examples of inspiration:
-Our website: https://www.ol-tiva.co.uk/
-Brindlecrest imagery - we are a Brindlecrest partner, so linking imagery with Brindlecrest would help.
-Competitor: https://www.morventapp.com/
-Ol-tiva Pulsecheck landing page: https://ol-tiva.tallyhive.com/

Full image files and AI/PNG files available on request

Slide 17 is a very rough design but if you can create something that is in line with the rest of the deck that would be great

Target Market(s)

Customer service teams and contact centres

Industry/Entity Type

Technology - Brindlecrest Ecosystem

Colors
0054AA
0677BA
7BADD7
CADEEF
E8F1F8

Requirements
Must have
• See description and branding doc
Nice to have
Should not have

```html
<!DOCTYPE html>
<html lang="en">
<head>
<meta charset="utf-8">
<title>Ol-tiva AI — Sales Deck</title>
<link href="https://fonts.googleapis.com/css2?family=Archivo+Black&family=Lexend:wght@300;500;600&family=Roboto:wght@300;400;500;700&display=swap" rel="stylesheet">
<style>
:root{
  --navy:#0054AA;
  --brand:#0677BA;
  --sky:#7BADD7;
  --mist:#CADEEF;
  --ice:#E8F1F8;
  --ink:#1c1c1c;
  --body:#333;
  --page:#d9d9d9;
  --stat:#1a73c8;
  --bar:#1d9be0;
}
*{margin:0;padding:0;box-sizing:border-box}
html,body{width:1200px;height:3976px;overflow:hidden;background:var(--page)}
body{position:relative;font-family:"Roboto",sans-serif;color:var(--body)}
.slide{position:absolute;left:83px;width:1032px;height:579px;background:#fff;overflow:hidden}
.abs{position:absolute}
.brand-mark{position:absolute;left:54px;top:39px;display:flex;align-items:center;gap:12px;font-family:"Lexend",sans-serif;font-weight:500;font-size:28px;letter-spacing:3px;color:#2b3a8c}
.brand-mark .dot{width:48px;height:48px;border-radius:50%;border:4px solid #2b3a8c}
.brand-mark.light{color:#fff}
.brand-mark.light .dot{border-color:#fff}
.heading{font-family:"Lexend",sans-serif;font-weight:600;color:var(--ink)}
.robot{position:absolute;border-radius:45% 45% 40% 40%;background:radial-gradient(circle at 45% 30%,#5cc3f5,#1a86d6 55%,#0d5fb0)}
.check-list{position:absolute;list-style:none}
.check-list li{display:flex;align-items:center;gap:14px;white-space:nowrap}
.check-list li svg{flex:none}
/* slide 1 */
.cover-title{left:54px;top:198px;width:510px;font-family:"Archivo Black",sans-serif;font-size:45px;line-height:54px;color:var(--ink);white-space:nowrap}
.cover-sub{left:54px;top:322px;font-family:"Lexend",sans-serif;font-weight:300;font-size:24px;line-height:36px;color:#555}
.partner-badge{left:584px;top:198px;width:70px;height:70px;border-radius:6px;background:#17325c;z-index:2}
.cover-halo{left:585px;top:97px;width:392px;height:392px;border-radius:50%;background:var(--ice)}
/* slide 2 */
.about-title{right:58px;top:44px;font-size:40px}
.about-facts{left:57px;top:176px;font-size:14px;line-height:20px;color:#222}
.about-facts p{margin-bottom:18px}
.stat-col{left:516px;width:200px;text-align:center}
.stat-num{font-family:"Lexend",sans-serif;font-weight:500;font-size:40px;color:var(--stat)}
.stat-cap{font-size:14px;line-height:20px;color:#222}
.client-card{position:absolute;top:369px;width:169px;height:88px;background:#fff;border-radius:6px;box-shadow:0 4px 18px rgba(0,0,0,.1);display:flex;align-items:center;justify-content:center;gap:8px;font-family:"Lexend",sans-serif;font-weight:500;font-size:22px;color:#2a2a2a}
.client-card .sq{width:14px;height:14px;background:#2a2a2a}
.tagline{left:0;width:100%;top:500px;text-align:center;font-weight:700;font-size:24px;color:var(--stat)}
/* slide 3 */
.divider{background:linear-gradient(135deg,#4a94dc,#2f7ccb 60%,#3b86d2)}
.divider-title{left:0;width:100%;top:228px;text-align:center;font-size:47px;line-height:61px;color:#fff}
/* slide 4 */
.impact-title{left:0;width:100%;top:150px;text-align:center;font-size:40px;line-height:54px}
.ring{position:absolute;top:288px;width:156px;height:156px;border-radius:50%;background:#fff;border:5px solid var(--ice);box-shadow:0 2px 10px rgba(0,84,170,.12);display:flex;align-items:center;justify-content:center;text-align:center;font-family:"Lexend",sans-serif;font-weight:500;color:var(--stat)}
.ring-cap{position:absolute;top:455px;width:320px;text-align:center;font-size:15px;color:#222}
/* slide 5 */
.report-title{left:54px;top:184px;font-size:38px;line-height:46px}
.report-list{left:54px;top:302px;font-size:17px;color:#222}
.report-list li{height:46px}
.dash-card{position:absolute;background:#fff;border-radius:8px;box-shadow:0 4px 16px rgba(0,0,0,.16);padding:8px 10px;font-size:9px;color:#333}
.dash-card .link{position:absolute;left:10px;bottom:6px;font-size:7px;color:var(--navy)}
/* slide 6 */
.chat-title{right:53px;top:40px;font-size:40px}
.chat-intro{left:519px;top:146px;width:458px;font-size:14.5px;line-height:26px;color:#333}
.chat-list{left:519px;top:284px;font-size:16.5px;color:#222}
.chat-list li{height:45.5px}
</style>
</head>
<body>

<svg width="0" height="0" style="position:absolute">
  <symbol id="tick" viewBox="0 0 16 16"><circle cx="8" cy="8" r="8" fill="#0677BA"/><path d="M4.5 8.2l2.3 2.3 4.7-4.8" stroke="#fff" stroke-width="1.8" fill="none"/></symbol>
</svg>

<!-- Cover -->
<section class="slide" style="top:93px">
  <div class="brand-mark"><span class="dot"></span>OL-TIVA AI</div>
  <h1 class="abs cover-title">Automated Quality<br>Assurance A.I</h1>
  <p class="abs cover-sub">Automate your Quality Assurance and<br>improve your insight by 50x</p>
  <div class="abs cover-halo"></div>
  <div class="robot" style="left:680px;top:70px;width:250px;height:440px" role="img" aria-label="Friendly blue robot mascot waving"></div>
  <div class="abs partner-badge" role="img" aria-label="Brindlecrest partner badge"></div>
</section>

<!-- About -->
<section class="slide" style="top:735px">
  <div class="brand-mark"><span class="dot"></span>OL-TIVA AI</div>
  <h2 class="abs heading about-title">A Bit About Us</h2>
  <div class="abs about-facts">
    <p>Trusted by companies across the globe to transform<br>their customer service</p>
    <p>Founded by contact centre leaders in 2015</p>
    <p>Brindlecrest CrestMarket Partner 5 Star-rated listing</p>
  </div>
  <div class="abs stat-col" style="top:140px">
    <div class="stat-num">100m+</div>
    <div class="stat-cap">AI predictions provided<br>so far by</div>
    <div class="stat-num" style="margin-top:4px">O - LIA</div>
    <div class="stat-cap">!Our AI Assistant</div>
  </div>
  <div class="robot" style="left:868px;top:137px;width:100px;height:180px" role="img" aria-label="Small blue robot assistant"></div>
  <div class="client-card" style="left:54px"><span class="sq"></span>Verantis</div>
  <div class="client-card" style="left:242px">calmorra</div>
  <div class="client-card" style="left:431px">pantrylane</div>
  <div class="client-card" style="left:619px">kidwallet</div>
  <div class="client-card" style="left:808px"><span class="sq"></span>Assessly</div>
  <p class="abs tagline">We take Complexity and bring Clarity</p>
</section>

<!-- Divider -->
<section class="slide divider" style="top:1377px">
  <div class="brand-mark light"><span class="dot"></span>OL-TIVA AI</div>
  <h2 class="abs heading divider-title">Why You Need AI-Powered<br>Quality Assurance</h2>
</section>

<!-- Impact -->
<section class="slide" style="top:2020px">
  <div class="brand-mark"><span class="dot"></span>OL-TIVA AI</div>
  <h2 class="abs heading impact-title">Resulting in a Lower NPS Score<br>Wasted Time &amp; Risk</h2>
  <div class="ring" style="left:98px;font-size:38px">98%</div>
  <div class="ring" style="left:436px;font-size:32px;line-height:38px">3<br>Months<br>+</div>
  <div class="ring" style="left:765px;font-size:38px">+£46k</div>
  <p class="ring-cap" style="left:16px">Of service cases missed every day</p>
  <p class="ring-cap" style="left:354px">Delay in QA training for agents</p>
  <p class="ring-cap" style="left:683px">Of wasted spend due to manual effort</p>
</section>

<!-- Reporting -->
<section class="slide" style="top:2662px">
  <svg class="abs" style="left:0;top:0" width="1032" height="579">
    <path d="M790 0 H1032 V579 H820 C860 420 880 200 790 0Z" fill="#E8F1F8"/>
    <path d="M790 0 C880 200 860 420 820 579" stroke="#0677BA" stroke-width="8" fill="none"/>
  </svg>
  <div class="brand-mark"><span class="dot"></span>OL-TIVA AI</div>
  <h2 class="abs heading report-title">Real-time Quality<br>Reporting</h2>
  <ul class="check-list report-list">
    <li><svg width="16" height="16"><use href="#tick"/></svg>At-a-glance reporting for leadership and QA teams</li>
    <li><svg width="16" height="16"><use href="#tick"/></svg>Track key KPIs for quality teams</li>
    <li><svg width="16" height="16"><use href="#tick"/></svg>Easily identify areas for improvement</li>
    <li><svg width="16" height="16"><use href="#tick"/></svg>Track appeals process</li>
  </ul>

  <div class="dash-card" style="left:503px;top:125px;width:294px;height:185px">
    Number of QA Forms by Team Member
    <svg class="abs" style="left:20px;top:30px" width="260" height="120">
      <line x1="10" y1="110" x2="250" y2="110" stroke="#ccc"/>
      <rect x="20" y="10" width="22" height="100" fill="var(--bar)"/>
      <rect x="48" y="30" width="22" height="80" fill="var(--bar)"/>
      <rect x="76" y="35" width="22" height="75" fill="var(--bar)"/>
      <rect x="104" y="48" width="22" height="62" fill="var(--bar)"/>
      <rect x="132" y="52" width="22" height="58" fill="var(--bar)"/>
      <rect x="160" y="60" width="22" height="50" fill="var(--bar)"/>
    </svg>
    <span class="link">View Report</span>
  </div>
  <div class="dash-card" style="left:682px;top:71px;width:294px;height:185px">
    Quality Assessment Scores by Month
    <svg class="abs" style="left:20px;top:30px" width="260" height="120">
      <line x1="10" y1="70" x2="250" y2="70" stroke="#ddd"/>
      <polyline points="20,26 45,22 70,30 95,24 120,25 145,30 170,24 195,22 220,24 245,28" stroke="var(--bar)" stroke-width="2" fill="none"/>
      <g font-size="8" fill="#555"><text x="14" y="90">Jan</text><text x="62" y="90">Mar</text><text x="110" y="90">May</text><text x="158" y="90">Jul</text><text x="200" y="90">Sep</text><text x="236" y="90">Nov</text></g>
    </svg>
    <span class="link">View Report</span>
  </div>
  <div class="dash-card" style="left:503px;top:333px;width:294px;height:194px">
    Quality Score by Section Last 30 days
    <svg class="abs" style="left:20px;top:30px" width="260" height="130">
      <line x1="10" y1="118" x2="250" y2="118" stroke="#ccc"/>
      <rect x="100" y="20" width="14" height="98" fill="#1d9be0"/>
      <rect x="114" y="20" width="14" height="98" fill="#0b2a55"/>
      <rect x="128" y="20" width="14" height="98" fill="#2bb3c7"/>
      <rect x="142" y="20" width="14" height="98" fill="#9fe3e8"/>
    </svg>
    <span class="link">View Report</span>
  </div>
  <div class="dash-card" style="left:682px;top:292px;width:294px;height:180px">
    Quality Score by agent last 90 days
    <svg class="abs" style="left:20px;top:28px" width="260" height="110">
      <line x1="10" y1="100" x2="250" y2="100" stroke="#ccc"/>
      <g fill="var(--bar)">
        <rect x="40" y="10" width="7" height="90"/><rect x="49" y="12" width="7" height="88"/><rect x="58" y="14" width="7" height="86"/><rect x="67" y="15" width="7" height="85"/><rect x="76" y="16" width="7" height="84"/><rect x="85" y="18" width="7" height="82"/><rect x="94" y="19" width="7" height="81"/><rect x="103" y="20" width="7" height="80"/><rect x="112" y="21" width="7" height="79"/><rect x="121" y="22" width="7" height="78"/><rect x="130" y="23" width="7" height="77"/><rect x="139" y="24" width="7" height="76"/><rect x="148" y="25" width="7" height="75"/><rect x="157" y="26" width="7" height="74"/><rect x="166" y="27" width="7" height="73"/><rect x="175" y="29" width="7" height="71"/><rect x="184" y="31" width="7" height="69"/><rect x="193" y="34" width="7" height="66"/><rect x="202" y="38" width="7" height="62"/><rect x="211" y="44" width="7" height="56"/><rect x="220" y="58" width="7" height="42"/>
      </g>
    </svg>
    <span class="link">View Report</span>
  </div>
</section>

<!-- Chatbot -->
<section class="slide" style="top:3304px">
  <div class="brand-mark"><span class="dot"></span>OL-TIVA AI</div>
  <h2 class="abs heading chat-title">Bespoke AI Chatbot</h2>
  <div class="robot" style="left:148px;top:139px;width:255px;height:409px" role="img" aria-label="Blue robot mascot with open arms"></div>
  <p class="abs chat-intro">On average, live chat and chatbots handle 69% of all contact centre conversations. On top of this, 31% of customer service organizations plan to start using chatbots within the next 18 months Stay ahead of the curve with chatbots that understand your products/services and customers' requests</p>
  <ul class="check-list chat-list">
    <li><svg width="16" height="16"><use href="#tick"/></svg>Trained on your knowledge base for accurate support</li>
    <li><svg width="16" height="16"><use href="#tick"/></svg>Elevate your self-serve offering</li>
    <li><svg width="16" height="16"><use href="#tick"/></svg>Reduce wait times &amp; cost-to-serve</li>
    <li><svg width="16" height="16"><use href="#tick"/></svg>Agents can focus on complex cases</li>
    <li><svg width="16" height="16"><use href="#tick"/></svg>Integrate with Brindlecrest and sites/portals</li>
    <li><svg width="16" height="16"><use href="#tick"/></svg>Increase CSAT &amp; NPS scores</li>
  </ul>
</section>

</body>
</html>
```